Consulting business card

*1) An Overview:* The business is simply a financial transaction wherein I
offer to provide advice to financial holders of commercial real estate
mortgages (which are sub-performing or non-performing), and said holders
are desirous of selling said mortgages which I will offer advice to said
holders in the purchase of said mortgages. Please note the attached copy
of a proposed line-by-line business card which starts with the 1st line
"RKW Advisory, LLC" with the 2nd line "Purchase of Commercial Mortgage
Loan" and the 3rd line "Sub-performing and Non-performing" is my desired
copy subject to any suggested changes. Please ignore the the copy below
the aforementioned proposed card/copy as it will be activated at a later
date.and advise
*2) The Target Market:* I contact and advise senior officers in banks,
insurance companies, and financial institutions such as CEOs, CFOs, COOs,
and Loan Mitigation Officers: the senior officers are tasked with the
removal of sub-performing and non-performing commercial real estate loans
from their real estate portfolios. The desired market is targeted at $1-10
million USD and located in the US.
*3) Design Specifics: *STYLE should be conservative and be representative
of the financial market contacts; COLOR might show a rich forest green
element, a gold foil accent, and subtle black printing, however,
alternatively, silver foil accent(s) with strong black print would seem in
harmony with the services offered, however, I would appreciate any artful
suggestions; IMAGERY should be subtle (no logo can be strong enough to make
an immediate impact): the quality should make the recipient feel he/she has
just met an experienced and competent financial adviser (I have over 55
years of successful financial and business experience).
720.217.6154davidfredrickjones@gmail.com

```html
<!DOCTYPE html>
<html lang="en">
<head>
<meta charset="utf-8">
<title>RKW Advisory – Business Card</title>
<link rel="stylesheet" href="https://fonts.googleapis.com/css2?family=Tinos:wght@400;700&display=swap">
<style>
  :root {
    --page-bg: #e9e7e3;
    --card-bg: #ffffff;
    --gold: #d4b532;
    --ink: #111111;
  }
  html, body {
    margin: 0;
    padding: 0;
    width: 1200px;
    height: 853px;
    overflow: hidden;
    background: var(--page-bg);
  }
  .business-card {
    position: absolute;
    left: 120px;
    top: 152px;
    width: 960px;
    height: 548px;
    background: var(--card-bg);
    box-shadow: 0 6px 24px rgba(0,0,0,0.18);
    font-family: "Tinos", "Times New Roman", serif;
    color: var(--ink);
  }
  .company-name {
    position: absolute;
    top: 62px;
    left: 0;
    width: 100%;
    margin: 0;
    text-align: center;
    font-weight: 400;
    font-size: 44px;
    color: var(--gold);
    padding-left: 40px;
    box-sizing: border-box;
  }
  .service-lines {
    position: absolute;
    top: 132px;
    left: 0;
    width: 100%;
    margin: 0;
    text-align: center;
    font-size: 32px;
    line-height: 40px;
    padding-left: 40px;
    box-sizing: border-box;
  }
  .name-row {
    position: absolute;
    left: 200px;
    right: 102px;
    top: 296px;
    display: flex;
    align-items: flex-start;
  }
  .person-name {
    margin: 0;
    flex: none;
    font-weight: 700;
    font-size: 38px;
    line-height: 44px;
    color: var(--gold);
    white-space: nowrap;
  }
  .divider {
    flex: 1;
    height: 4px;
    margin-left: 16px;
    margin-top: 14px;
    background: var(--gold);
  }
  .contact-list {
    position: absolute;
    right: 100px;
    top: 360px;
    margin: 0;
    padding: 0;
    list-style: none;
    text-align: right;
    font-size: 25px;
    line-height: 36px;
  }
  .contact-item {
    position: relative;
  }
  .contact-icon {
    position: absolute;
    right: -32px;
    top: 9px;
    width: 16px;
    height: 16px;
  }
</style>
</head>
<body>
  <section class="business-card">
    <h1 class="company-name">RKW Advisory</h1>
    <p class="service-lines">Purchase of Commercial Mortgage Loan<br>Sub-performing and Non-performing</p>
    <div class="name-row">
      <p class="person-name">Jane Morrow</p>
      <div class="divider"></div>
    </div>
    <ul class="contact-list">
      <li class="contact-item">555.304.8827
        <svg class="contact-icon" viewBox="0 0 16 16" aria-hidden="true">
          <rect width="16" height="16" fill="#d4b532"/>
          <rect x="5" y="3" width="6" height="10" rx="1" fill="none" stroke="#fff" stroke-width="1.4"/>
        </svg>
      </li>
      <li class="contact-item">tomasheraldwick@mailbox.example
        <svg class="contact-icon" viewBox="0 0 16 16" aria-hidden="true">
          <rect width="16" height="16" fill="#d4b532"/>
          <rect x="3" y="5" width="10" height="7" fill="none" stroke="#fff" stroke-width="1.3"/>
          <path d="M3 5 L8 9 L13 5" fill="none" stroke="#fff" stroke-width="1.3"/>
        </svg>
      </li>
    </ul>
  </section>
</body>
</html>
```